Structural Engineering Business Card

Brookvane Drafting does residential house plans for clients in Central Florida. Would like simple but elegant business card that is appropriate for a house plan engineering company. Prefer black business card with black/white them but open to other shades of blue. I uploaded a sample card that I came across that looked good but please come up with your own creative designs.

Contact Information for Business Card

Name, Title, Phone, Email, Address, website

```html
<!DOCTYPE html>
<html lang="en">
<head>
<meta charset="utf-8">
<title>Brookvane Drafting — Business Card</title>
<link href="https://fonts.googleapis.com/css2?family=Poppins:wght@300;400;700;800&display=swap" rel="stylesheet">
<style>
  :root {
    --backdrop: #1c1c1c;
    --card: #0b0b0b;
    --card-edge: #2a2a2a;
    --ink: #ffffff;
    --ink-soft: #d9d9d9;
    --rule: #8a8a8a;
  }
  * { margin: 0; padding: 0; box-sizing: border-box; }
  html, body {
    width: 1200px; height: 900px; overflow: hidden;
    background: var(--backdrop);
    font-family: "Poppins", sans-serif;
    color: var(--ink);
  }
  .canvas {
    width: 1200px; height: 900px;
    display: flex; flex-direction: column;
    align-items: center; justify-content: center; gap: 48px;
  }
  .card {
    width: 620px; height: 354px;
    background: var(--card);
    border: 1px solid var(--card-edge);
    border-radius: 22px;
    position: relative;
    overflow: hidden;
  }
  /* front side */
  .card--front { display: flex; align-items: center; }
  .front__brand {
    flex: none;
    width: 320px; padding: 0 24px 0 34px;
    display: flex; align-items: center; gap: 10px;
    margin-top: 60px;
  }
  .brand-mark { width: 14px; height: 14px; background: var(--ink); flex: none; }
  .brand-name {
    font-weight: 800; font-size: 18px; letter-spacing: 0.3px;
    text-transform: uppercase; color: var(--ink); white-space: nowrap;
  }
  .front__rule {
    flex: none;
    width: 1px; height: 220px; background: var(--rule);
  }
  .front__details { padding-left: 28px; padding-right: 20px; }
  .person__name { font-weight: 700; font-size: 22px; letter-spacing: 0.5px; line-height: 1.1; text-transform: uppercase; white-space: nowrap; }
  .person__title { font-weight: 300; font-size: 15px; color: var(--ink-soft); margin-bottom: 18px; }
  .contact-list { list-style: none; }
  .contact-list li {
    display: flex; align-items: center; gap: 8px;
    font-size: 15px; font-weight: 400; line-height: 1.5;
    white-space: nowrap;
  }
  .contact-list svg { width: 14px; height: 14px; flex: none; }
  .address { font-size: 15px; line-height: 1.4; margin-top: 14px; white-space: nowrap; }
  /* back side */
  .card--back { display: flex; align-items: center; justify-content: center; }
  .card--back .brand-name { font-size: 38px; }
  .card--back .brand-mark { width: 24px; height: 24px; }
  .card--back .back__brand { display: flex; align-items: center; gap: 16px; }
</style>
</head>
<body>
<main class="canvas">
  <section class="card card--front" aria-label="Business card front">
    <div class="front__brand">
      <span class="brand-mark"></span>
      <span class="brand-name">Brookvane Drafting</span>
    </div>
    <div class="front__rule"></div>
    <div class="front__details">
      <p class="person__name">Daniel Marsh</p>
      <p class="person__title">Managing Director</p>
      <ul class="contact-list">
        <li>
          <svg viewBox="0 0 24 24" fill="var(--ink)" aria-hidden="true"><path d="M6.6 10.8a15.1 15.1 0 0 0 6.6 6.6l2.2-2.2a1 1 0 0 1 1-.25 11.4 11.4 0 0 0 3.6.57 1 1 0 0 1 1 1V20a1 1 0 0 1-1 1A17 17 0 0 1 3 4a1 1 0 0 1 1-1h3.5a1 1 0 0 1 1 1c0 1.250.2 2.450.57 3.57a1 1 0 0 1-.25 1z"/></svg>
          044-555 010 234
        </li>
        <li>
          <svg viewBox="0 0 24 24" aria-hidden="true"><rect x="2" y="5" width="20" height="14" fill="var(--ink)"/><path d="M2 5l10 8 10-8" fill="none" stroke="var(--card)" stroke-width="1.6"/></svg>
          info@brookvane.com
        </li>
        <li>
          <svg viewBox="0 0 24 24" fill="none" stroke="var(--ink)" stroke-width="1.8" aria-hidden="true"><circle cx="12" cy="12" r="9.5"/><ellipse cx="12" cy="12" rx="4" ry="9.5"/><path d="M2.5 12h19"/></svg>
          www.brookvane.com
        </li>
      </ul>
      <p class="address">421, Cypress Hollow Road<br>Orlando, FL 32801</p>
    </div>
  </section>

  <section class="card card--back" aria-label="Business card back">
    <div class="back__brand">
      <span class="brand-mark"></span>
      <span class="brand-name">Brookvane Drafting</span>
    </div>
  </section>
</main>
</body>
</html>
```